Belvascotravel.com web design project + logo design

Hi,

We are a Russian online tour operator - sunkettle.com

We are looking to tranmsfer our domain to belvascotravel.com. The website and logo need to be belvascoesque - we are not looking to change our functionality, but we need to make the website much more attracitve to clients, much more wild looking but at the same time remaining a professional travel company.

The main concept of the website should be innovative travel (as belvasco was an innovator). Alternatively, you could go down the artist route and go down the draw / design your own tour road.

On our website the customer is able to combine travel services (hotels, flights, Visa services, and soon chauffeur, car rental etc...) put it into their basket (the basket definitely has to look better than it is at the moment) and pay for it in one go by card.

We are also stressin our customer support with web chat, call centre etc... (call centre number at the top of the page)

We aim to provide an easy user experience, but we need to make it have some more style, so I will be waiting for what you guys can come up with.
Let me know if you have any questions - skype is: mrdolbarin

Industry/Entity Type

It Company

Requirements
Must have
• It is quite a simple task - to take the existing website sunkettle.com and belvascosize it to create belvascotravel.com, the functionality of the website will remain the same and there are not many pages in the website. Homepage, Checkout step1, Checkout step 2 (you can view both of these if you select a service) and the generic pages for T&C''s, Privacy policy etc...

IMPORTANT UPDATE

We are also looking at how the search results will look in the designs, (please do a search on our website for hotel / flight)

```html
<!DOCTYPE html>
<html lang="en">
<head>
<meta charset="utf-8">
<title>Belvasco Travel</title>
<link rel="stylesheet" href="https://fonts.googleapis.com/css2?family=Roboto:wght@300;400;500;700&display=swap">
<style>
:root{
  --pink:#ec3f97;
  --blue:#14b4ee;
  --dark:#4a4a4a;
  --ink:#333;
  --muted:#777;
  --line:#cfcfcf;
  --header:#d4d4d4;
  --soft:#ececec;
  --white:#fff;
  --footer-bar:#3a3a3a;
}
*{box-sizing:border-box;margin:0;padding:0}
html,body{width:756px;height:1200px;overflow:hidden}
body{position:relative;background:var(--white);font-family:"Roboto",Arial,sans-serif;color:var(--ink)}
.abs{position:absolute}
.site-header{left:0;top:0;width:756px;height:367px;background:linear-gradient(#dadada,#cfcfcf)}
.skyline{left:126px;top:50px;width:504px;height:140px;background:linear-gradient(180deg,rgba(255,255,255,0),rgba(245,245,245,.75));}
.brand{left:126px;top:12px;display:flex;align-items:center;gap:6px}
.brand-mark{width:44px;height:44px;border-radius:50%;background:var(--white)}
.brand-name{line-height:1}
.brand-name b{display:block;font-weight:500;font-size:24px;color:#3f3f3f}
.brand-name span{display:block;font-weight:300;font-size:17px;color:var(--pink)}
.lang{left:592px;top:12px;width:38px;height:9px;background:var(--white);border:1px solid #bbb;font-size:6px;padding-left:2px;line-height:7px}
.lang::after{content:"";position:absolute;right:1px;top:1px;width:5px;height:5px;background:#444}
.phone{left:490px;top:28px;display:flex;gap:6px}
.phone-number{font-size:17px;font-weight:300;color:#444;line-height:1}
.phone-hours{font-size:7px;color:var(--pink);margin-top:1px}
.side-btn{left:584px;width:47px;height:18px;background:var(--white);border:1px solid #bbb;font-size:6px;color:var(--pink);display:flex;align-items:center;gap:4px;padding-left:4px}
.side-btn i{width:7px;height:7px;background:#333;border-radius:50%}
.tab{top:172px;height:18px;font-size:7px;color:#eee;background:#5a5a5a;display:flex;align-items:center;justify-content:center}
.tab.active{background:var(--blue);color:#111}
.booking{left:126px;top:190px;width:371px;height:128px;background:var(--white);border-radius:0 0 3px 3px}
.lbl{font-size:7px;color:var(--pink)}
.field{height:15px;border:2px solid #ddd;background:var(--white);font-size:6px;color:#555;padding-left:4px;line-height:11px;white-space:nowrap}
.field.muted{color:#bbb}
.select::after{content:"";position:absolute;right:2px;top:2px;width:7px;height:7px;background:#444}
.tiny{font-size:5px;color:#aaa}
.check{width:6px;height:6px;border:1px solid #bbb;background:#f4f4f4}
.btn-dark{background:var(--dark);color:#fff;display:flex;align-items:center;justify-content:center;border-bottom:2px solid #222}
.basket{left:502px;top:191px;width:128px;height:127px;background:var(--white)}
.basket-head{height:19px;background:var(--blue);font-size:12px;text-align:center;line-height:19px;color:#222}
.basket-pay{left:0;top:72px;width:128px;height:18px;background:var(--pink);color:#fff;font-size:8px;text-align:center;line-height:18px}
.cards{left:16px;top:94px;display:flex;gap:3px}
.cards span{width:17px;height:11px;background:#e6e6e6;border:1px solid #bbb}
.basket-foot{left:0;top:110px;width:128px;height:17px;background:#5a5a5a;color:#fff;font-size:8px;text-align:center;line-height:17px}
.search-tab{left:304px;top:336px;width:148px;height:31px;background:var(--white);text-align:center;font-size:9px;padding-top:3px}
.search-tab em{display:inline-block;font-style:normal;background:var(--pink);color:#fff;font-size:8px;padding:1px 5px;margin-top:2px}
.quick-search{left:0;top:367px;width:756px;height:92px;background:linear-gradient(#fff,#f2f2f2)}
.step{height:13px;background:var(--blue);font-size:6px;color:#111;padding:3px 4px;white-space:nowrap}
.opt{font-size:5.5px;color:#444;display:flex;gap:6px;align-items:center}
.spin{width:37px;height:15px;border:1px solid #ccc;font-size:6px;padding:3px 4px;background:#fff}
.spin::after{content:"";position:absolute;right:4px;top:3px;border:3px solid transparent;border-bottom:0;border-top:7px solid #222}
.rule{left:0;top:458px;width:756px;height:2px;background:var(--blue)}
.section-soft{background:var(--soft)}
.tag{height:24px;background:#5c5c5c;color:#fff;font-size:15px;font-weight:300;padding:0 9px;line-height:24px}
.title-pink{color:var(--pink);font-weight:300;text-align:center;width:756px;left:0;white-space:nowrap}
.visa-item{font-size:12px;color:#333;text-align:center;width:200px}
.btn-blue{width:54px;height:18px;background:var(--blue);color:#fff;font-size:8px;text-align:center;line-height:18px;border-bottom:2px solid #0b8fc0}
.ticket-art{left:126px;top:680px;width:504px;height:205px;background:linear-gradient(180deg,#f6f6f6,#fbfbfb 60%,#eeeeee);}
.ticket-title{left:225px;top:755px;width:306px;height:38px;background:#fff;border:1px solid #ddd;color:var(--pink);font-size:23px;font-weight:300;text-align:center;line-height:36px;white-space:nowrap;overflow:hidden}
.ticket-text{left:126px;top:806px;width:504px;height:44px;background:#fff;border:1px solid #ddd;font-size:6.6px;color:#666;line-height:10px;padding:5px 9px}
.hotel-text{left:126px;top:998px;width:504px;font-size:6.6px;color:#666;line-height:11px}
.offers{left:474px;top:1078px;width:156px;height:42px;background:#fff;padding:2px 8px}
.offers h3{font-size:9px;font-weight:500;color:#222}
.offers-input{left:8px;top:18px;width:140px;height:14px;background:var(--pink);border-radius:7px;font-size:5.5px;color:#fde;padding:4px 6px}
.offers-send{left:98px;top:18px;width:43px;height:14px;background:#111;border-radius:7px;color:#fff;font-size:6px;text-align:center;line-height:14px}
.site-footer{left:0;top:1096px;width:756px;height:84px;background:var(--blue);color:#fff}
.foot-col h4{font-size:8px;font-weight:400;color:#111;margin-bottom:9px}
.foot-col p{font-size:5.5px;line-height:10px;display:flex;align-items:center;gap:4px;white-space:nowrap}
.foot-col p i{width:7px;height:7px;border-radius:50%;background:#fff}
.foot-brand{left:528px;top:36px;display:flex;align-items:center;gap:5px;line-height:1}
.foot-brand .dot{width:34px;height:34px;border-radius:50%;background:#fff}
.foot-brand b{display:block;font-size:17px;font-weight:500}
.foot-brand span{display:block;font-size:12px;font-weight:300}
.legal{left:0;top:1180px;width:756px;height:20px;background:var(--footer-bar);color:#ddd;font-size:5.5px;text-align:center;line-height:20px}
</style>
</head>
<body>

<header class="site-header abs">
  <div class="skyline abs" role="img" aria-label="Sketched skyline of world landmarks with a passenger plane"></div>
  <div class="brand abs"><span class="brand-mark"></span><div class="brand-name"><b>Belvasco</b><span>Travel</span></div></div>
  <div class="lang abs">English</div>
  <div class="phone abs">
    <svg width="20" height="22" viewBox="0 0 20 22"><path d="M4 1 L8 6 L6 9 Q8 14 13 16 L16 13 L20 17 L16 21 Q4 19 1 5 Z" fill="#ec3f97"/></svg>
    <div><div class="phone-number">8-800-555-0142</div><div class="phone-hours">(Mon-Fri) Hours: 9:00 am - 18:00</div></div>
  </div>
  <div class="side-btn abs" style="top:68px"><i></i>My Tour</div>
  <div class="side-btn abs" style="top:90px"><i></i>Web Chat</div>

  <div class="tab active abs" style="left:126px;width:56px">TICKETS</div>
  <div class="tab abs" style="left:183px;width:57px">INFO</div>
  <div class="tab abs" style="left:241px;width:54px">HOTELS</div>

  <form class="booking abs">
    <span class="lbl abs" style="left:10px;top:22px">Whence</span>
    <div class="field muted abs" style="left:59px;top:15px;width:105px">Type...</div>
    <span class="lbl abs" style="left:10px;top:44px">There</span>
    <div class="field abs" style="left:59px;top:37px;width:105px">30-5-2013</div>
    <span class="tiny abs" style="left:67px;top:57px">Men</span>
    <span class="tiny abs" style="left:102px;top:57px">Women</span>
    <span class="tiny abs" style="left:141px;top:57px">Children</span>
    <span class="lbl abs" style="left:10px;top:71px">Passengers</span>
    <div class="field select abs" style="left:59px;top:67px;width:24px">1</div>
    <div class="field select abs" style="left:101px;top:67px;width:24px">1</div>
    <div class="field select abs" style="left:141px;top:67px;width:24px">1</div>

    <span class="lbl abs" style="left:183px;top:22px">Where</span>
    <div class="field muted abs" style="left:225px;top:15px;width:105px">Type...</div>
    <span class="lbl abs" style="left:183px;top:44px">Back</span>
    <div class="field abs" style="left:225px;top:37px;width:61px">16-6-2013</div>
    <span class="check abs" style="left:293px;top:37px"></span><span class="tiny abs" style="left:304px;top:37px;color:#555">Back</span>
    <span class="check abs" style="left:293px;top:46px"></span><span class="tiny abs" style="left:304px;top:46px;color:#555">One way</span>
    <span class="lbl abs" style="left:183px;top:71px">Class</span>
    <div class="field select abs" style="left:225px;top:67px;width:105px">Economy</div>

    <div class="btn-dark abs" style="left:150px;top:98px;width:72px;height:22px;font-size:12px;font-weight:300">Search</div>
  </form>

  <aside class="basket abs">
    <div class="basket-head">BASKET</div>
    <svg class="abs" style="left:38px;top:24px" width="52" height="44" viewBox="0 0 52 44" aria-label="Basket">
      <path d="M2 4 H10 L16 28 H44 L49 10 H12" fill="none" stroke="#555" stroke-width="2"/>
      <path d="M14 14 H46 M15 20 H44 M24 10 V28 M34 10 V28" stroke="#bbb" stroke-width="1"/>
      <circle cx="20" cy="36" r="3.5" fill="none" stroke="#555" stroke-width="2"/>
      <circle cx="40" cy="36" r="3.5" fill="none" stroke="#555" stroke-width="2"/>
    </svg>
    <div class="basket-pay abs">Payment</div>
    <div class="cards abs"><span></span><span></span><span></span><span></span><span></span></div>
    <div class="basket-foot abs">*Pricing</div>
  </aside>

  <div class="search-tab abs">Search for A Hotel / Flight<br><em>Book Now</em></div>
</header>

<section class="quick-search abs">
  <div class="step abs" style="left:126px;top:16px;width:40px">01. What?</div>
  <div class="opt abs" style="left:126px;top:36px"><span class="check"></span>Hotels</div>
  <div class="opt abs" style="left:126px;top:50px"><span class="check"></span>Flights</div>
  <div class="opt abs" style="left:126px;top:64px"><span class="check"></span>Cars</div>

  <div class="step abs" style="left:213px;top:16px;width:40px">02. Where?</div>
  <div class="field select muted abs" style="left:213px;top:36px;width:130px;font-size:5.5px">Choose a City</div>

  <div class="step abs" style="left:396px;top:16px;width:41px">03. When?</div>
  <div class="field muted abs" style="left:396px;top:36px;width:58px;font-size:5.5px;border-width:1px">Check In</div>
  <div class="field muted abs" style="left:396px;top:55px;width:58px;font-size:5.5px;border-width:1px">Check Out</div>

  <div class="step abs" style="left:507px;top:16px;width:40px">04. Who?</div>
  <span class="abs" style="left:507px;top:36px;font-size:6px">Rooms</span>
  <span class="abs" style="left:550px;top:36px;font-size:6px">Adults</span>
  <span class="abs" style="left:593px;top:36px;font-size:6px">Child</span>
  <div class="spin abs" style="left:507px;top:44px">01</div>
  <div class="spin abs" style="left:550px;top:44px">01</div>
  <div class="spin abs" style="left:593px;top:44px">01</div>

  <div class="btn-dark abs" style="left:570px;top:78px;width:62px;height:16px;font-size:8px">Search</div>
</section>
<div class="rule abs"></div>

<section class="section-soft abs" style="left:0;top:480px;width:756px;height:198px">
  <div class="tag abs" style="left:126px;top:11px">INFO</div>
  <h2 class="title-pink abs" style="top:42px;font-size:25px">There are two option apply for visa</h2>
  <p class="visa-item abs" style="left:177px;top:93px">1. Oformlenie visa “Online”</p>
  <p class="visa-item abs" style="left:408px;top:93px">2. Visa “Myself.”</p>
  <svg class="abs" style="left:267px;top:124px" width="20" height="30" viewBox="0 0 20 30"><path d="M8 0 H12 V18 H19 L10 30 L1 18 H8 Z" fill="#111"/></svg>
  <svg class="abs" style="left:498px;top:124px" width="20" height="30" viewBox="0 0 20 30"><path d="M8 0 H12 V18 H19 L10 30 L1 18 H8 Z" fill="#111"/></svg>
  <div class="btn-blue abs" style="left:250px;top:163px">Click Here</div>
  <div class="btn-blue abs" style="left:481px;top:163px">Click Here</div>
</section>

<section class="abs" style="left:0;top:678px;width:756px;height:219px">
  <div class="ticket-art abs" style="top:2px" role="img" aria-label="Faint sketch of landmarks and a plane behind the tickets text"></div>
  <div class="tag abs" style="left:126px;top:11px">TICKETS</div>
</section>
<h2 class="ticket-title abs">Flights from Tours designer.</h2>
<p class="ticket-text abs">On our site you can consider offers from different airlines and purchase tickets according to your wishes and budget. Plan dates of departures and arrivals c in any country, filling the cells you want, Tour Designer automatically displays your program in the calendar. On Tour Designer You can create any tour, including round-the-world and pay for all the services a single payment.</p>

<section class="section-soft abs" style="left:0;top:897px;width:756px;height:165px">
  <div class="tag abs" style="left:126px;top:10px">HOTELS</div>
  <h2 class="title-pink abs" style="top:50px;font-size:26px">Hotels by City Builder.</h2>
</section>
<p class="hotel-text abs">Our site offers a wide selection of hotels located in different countries and continents of the world. You can choose and book all kinds of accommodation options, according to your wishes and budget. pursue their dreams! We have created for you the most convenient framework for planning a vacation or business trip. Tour Builder saves your time now to buy a package tour you can just 3 simple steps: Choose the services Confirm requested services, payment of a single payment. A complete set of documents confirming the purchase tour package will be on our website in your personal account, send documents to "Print".</p>

<footer class="site-footer abs">
  <div class="foot-col abs" style="left:126px;top:10px"><h4>View Site</h4><p>Home</p><p>About Us</p><p>Form</p><p>Contacts</p></div>
  <div class="foot-col abs" style="left:190px;top:10px"><h4>Follow Us</h4><p><i></i>Friendwall</p><p><i></i>Chirpline</p><p><i></i>Blog</p></div>
  <div class="foot-col abs" style="left:264px;top:10px"><h4>Contact Us</h4><p>+7 (495) 555-01-86</p><p>8-800-555-0142</p><p>info@belvascotravel.com</p></div>
  <div class="foot-col abs" style="left:366px;top:10px"><h4>Find Us</h4><p>Sunkettle Tours Limited 14</p><p>Harlow Row London,</p><p>E9 4QX UK</p></div>
  <div class="foot-brand abs"><span class="dot"></span><div><b>Belvasco</b><span>Travel</span></div></div>
</footer>
<div class="offers abs">
  <h3>Exclusive Offers</h3>
  <div class="offers-input abs">Email Address</div>
  <div class="offers-send abs">Send</div>
</div>
<div class="legal abs">© 2012–2013 BelvascoTravel, Terms &amp; Conditions : Privacy Policy</div>

</body>
</html>
```